Calvanto Group Real Estate Company business cards

New business card design, we are generally happy with the basic layout of the existing front of business card, (feel free to change) but require a head shot photo on the back side.

http://www.calvanto.com.au/

Attached logos, and existing business card

------------------------------

Target Market(s)

Real estate

Industry/Entity Type

Real Estate

Contact Information for Business Card

Standard size double sided

Font styles to use
Other font styles liked:
• Futura

Requirements
Must have
• Photo head shot on the back side
Nice to have
• yes
Should not have
• No

```html
<!DOCTYPE html>
<html lang="en">
<head>
<meta charset="utf-8">
<title>Calvanto Group – Business Cards</title>
<link href="https://fonts.googleapis.com/css2?family=Open+Sans:wght@400;600;700&display=swap" rel="stylesheet">
<style>
  :root {
    --stage: #3b3b3b;
    --paper: #fbfbfb;
    --indigo: #2e1d5e;
    --indigo-deep: #2b1a5a;
    --orange: #f08a1c;
    --ink: #4a4a4a;
    --rule: #e9b27a;
    --white: #ffffff;
  }
  * { margin: 0; padding: 0; box-sizing: border-box; }
  html, body { width: 1200px; height: 750px; overflow: hidden; }
  body {
    background: var(--stage);
    font-family: "Open Sans", sans-serif;
    position: relative;
  }
  .card {
    position: absolute;
    top: 228px;
    width: 462px;
    height: 263px;
  }
  .card--front { left: 124px; background: var(--paper); color: var(--ink); }
  .card--back { left: 618px; background: var(--indigo-deep); overflow: hidden; }

  .brand {
    position: absolute;
    left: 250px;
    top: 34px;
    width: 182px;
    text-align: center;
  }
  .brand__name {
    display: flex;
    align-items: center;
    justify-content: center;
    gap: 8px;
    font-size: 36px;
    font-weight: 600;
    color: var(--indigo);
    line-height: 1;
    letter-spacing: -0.5px;
  }
  .brand__mark { width: 10px; height: 10px; background: var(--orange); display: inline-block; }
  .brand__tagline {
    margin-top: 16px;
    font-size: 11px;
    font-weight: 600;
    color: var(--indigo);
    word-spacing: 4px;
  }
  .brand__tagline span { margin: 0 3px; }

  .person { position: absolute; left: 24px; top: 138px; }
  .person__name { font-size: 17px; font-weight: 600; color: var(--indigo); line-height: 1.2; }
  .person__role { font-size: 12.5px; color: var(--orange); line-height: 1.2; }
  .divider {
    position: absolute; left: 72px; top: 171px;
    width: 362px; height: 1px; background: var(--rule);
  }

  .contacts { position: absolute; left: 24px; top: 186px; list-style: none; }
  .contacts li {
    display: flex; align-items: center; gap: 6px;
    height: 17.5px; font-size: 12px; color: var(--ink);
  }
  .contacts svg { width: 12px; height: 12px; fill: var(--indigo); flex: none; }

  .company { position: absolute; right: 24px; top: 204px; text-align: right; }
  .company__name { font-size: 12.5px; font-weight: 600; color: var(--ink); line-height: 1.4; }
  .company__abn { font-size: 12.5px; color: var(--ink); line-height: 1.4; }

  .back-brand {
    position: absolute; left: 36px; top: 150px;
    font-size: 40px; font-weight: 600; color: var(--orange); line-height: 1;
  }
  .back-url {
    position: absolute; left: 35px; top: 230px;
    font-size: 12px; letter-spacing: 1.4px; color: var(--white);
  }
  .headshot {
    position: absolute; left: 276px; top: 14px;
    width: 182px; height: 249px;
    background: linear-gradient(180deg, #3a3370 0%, #2a2f5a 45%, #1f2b4d 100%);
  }
</style>
</head>
<body>
  <section class="card card--front" aria-label="Business card front">
    <div class="brand">
      <div class="brand__name"><span class="brand__mark"></span>calvanto</div>
      <div class="brand__tagline">Buy<span>|</span>Sell<span>|</span>Rent</div>
    </div>

    <div class="person">
      <div class="person__name">Daniel Tran</div>
      <div class="person__role">Director</div>
    </div>
    <div class="divider"></div>

    <ul class="contacts">
      <li>
        <svg viewBox="0 0 24 24" aria-hidden="true"><path d="M6.6 10.8a15.1 15.1 0 0 0 6.6 6.6l2.2-2.2c.3-.3.7-.4 1-.2 1.1.4 2.3.6 3.6.6.6 0 1 .4 1 1V20c0 .6-.4 1-1 1A17 17 0 0 1 3 4c0-.6.4-1 1-1h3.5c.6 0 1 .4 1 1 0 1.3.2 2.5.6 3.6.1.3 0 .7-.2 1z"/></svg>
        0400 555 218
      </li>
      <li>
        <svg viewBox="0 0 24 24" aria-hidden="true"><path d="M2 5h20v14H2z M4 7v.5l8 5 8-5V7l-8 5z" fill-rule="evenodd"/></svg>
        daniel.tran@calvanto.com.au
      </li>
      <li>
        <svg viewBox="0 0 24 24" aria-hidden="true"><path d="M12 2a10 10 0 1 0 0 20 10 10 0 0 0 0-20zm-1 17.9A8 8 0 0 1 4.2 10.2L9 15v1a2 2 0 0 0 2 2zm6.9-2.5A2 2 0 0 0 16 16h-1v-3a1 1 0 0 0-1-1H8v-2h2a1 1 0 0 0 1-1V7h2a2 2 0 0 0 2-2v-.4a8 8 0 0 1 2.9 12.8z"/></svg>
        www.calvanto.com.au
      </li>
    </ul>

    <div class="company">
      <div class="company__name">Calvanto Group</div>
      <div class="company__abn">ABN: 12 345 678 901</div>
    </div>
  </section>

  <section class="card card--back" aria-label="Business card back">
    <div class="back-brand">calvanto</div>
    <div class="back-url">www.calvanto.com.au</div>
    <div class="headshot" role="img" aria-label="Head shot photo of the director in a navy suit and blue tie"></div>
  </section>
</body>
</html>
```